Flyer for Tallow Brisko - Design Agency

We need a 4-page square flyer measuring 14.8x14.8cm per page, to fold out, for a design agency targeting small businesses.
The design should be very modern. There shouldn't be too much content visible.
The background should be black. The color of the logo (attached) can also be used. The content is also attached and divided per page. We are open to alternative suggestions regarding the division.

```html
<!DOCTYPE html>
<html lang="de">
<head>
<meta charset="utf-8">
<title>Tallow Brisko – Faltflyer</title>
<link rel="stylesheet" href="https://fonts.googleapis.com/css2?family=Big+Shoulders+Display:wght@700;800;900&family=Poppins:wght@400;500;600;700&display=swap">
<style>
:root{
  --stage:#e4e4e6;
  --ink:#05040c;
  --navy:#0b0d3a;
  --cyan:#3ef0e6;
  --purple:#7b2cf5;
  --violet:#5a22c9;
  --magenta:#c23bd8;
  --white:#ffffff;
  --muted:#d8d8ea;
}
*{margin:0;padding:0;box-sizing:border-box}
html,body{width:1200px;height:2213px;overflow:hidden;background:var(--stage)}
body{position:relative;font-family:"Poppins",sans-serif;color:var(--white)}
.spread{position:absolute;left:70px;width:1060px;height:532px;overflow:hidden;
  background:radial-gradient(ellipse at 78% 45%,#14157a 0%,var(--navy) 35%,var(--ink) 75%);
  box-shadow:0 18px 40px rgba(0,0,0,.25)}
.spread--outer{top:540px}
.spread--inner{top:1142px;background:radial-gradient(ellipse at 80% 40%,#12136a 0%,var(--navy) 40%,var(--ink) 80%)}
.page{position:absolute;top:0;width:530px;height:532px}
.page--left{left:0}
.page--right{left:530px}
.fold{position:absolute;left:529px;top:0;width:2px;height:532px;background:rgba(255,255,255,.04)}
.wordmark{position:absolute;font-family:"Poppins",sans-serif;font-weight:500;color:var(--cyan);text-align:center;line-height:.9;letter-spacing:-.5px}
.display{font-family:"Big Shoulders Display",sans-serif;font-weight:900;text-transform:uppercase;line-height:1}
.art{position:absolute;border-radius:18px}
.echo{position:absolute;left:150px;font-family:"Big Shoulders Display",sans-serif;font-weight:900;font-size:38px;line-height:1;text-transform:uppercase;color:transparent;-webkit-text-stroke:1px rgba(123,44,245,.55);letter-spacing:1px;white-space:nowrap}
.brand-title{position:absolute;left:150px;top:228px;font-size:44px;color:var(--cyan);letter-spacing:.5px;white-space:nowrap}
.tagline-box{position:absolute;left:74px;top:276px;width:376px;height:60px;border:1.5px solid var(--violet);border-radius:10px;display:flex;align-items:center;justify-content:center;font-size:16px;font-weight:500;white-space:nowrap}
.band{position:absolute;height:34px;display:flex;align-items:center;padding-left:14px;font-weight:600;line-height:1.05;white-space:nowrap}
.band--purple{background:linear-gradient(90deg,var(--purple) 0%,var(--purple) 45%,rgba(123,44,245,0) 100%)}
.band--cyan{background:linear-gradient(90deg,var(--cyan) 0%,var(--cyan) 45%,rgba(62,240,230,0) 100%);color:var(--ink)}
.contact{position:absolute;left:37px;font-size:13px;line-height:1.15;display:flex;gap:8px;align-items:flex-start;white-space:nowrap}
.contact svg{flex:none;margin-top:2px}
.owner{position:absolute;left:263px;top:418px;width:250px;font-size:24px;line-height:1.05;white-space:nowrap}
.owner small{font-size:16px;display:block;margin-bottom:3px}
.web-pill{position:absolute;left:263px;top:474px;width:235px;height:20px;background:var(--cyan);color:var(--ink);font-size:14px;letter-spacing:1.6px;display:flex;align-items:center;justify-content:center;white-space:nowrap}
.cover-line{position:absolute;left:0;width:530px;text-align:center;color:var(--white);white-space:nowrap}
.cover-line--small{top:346px;font-size:46px;font-weight:800}
.cover-line--big{top:392px;font-size:72px;color:var(--cyan);letter-spacing:2px;text-shadow:4px 4px 0 var(--purple)}
.cover-web{position:absolute;top:480px;left:0;width:530px;text-align:center;font-size:17px;line-height:1.2;letter-spacing:3px}
.headline{position:absolute;left:37px;top:28px;font-size:40px;color:var(--cyan);letter-spacing:.5px;white-space:nowrap}
.lead{position:absolute;left:37px;top:80px;font-size:17px;line-height:1.2}
.lead strong{font-weight:700;text-transform:uppercase;display:block}
.quote-box{position:absolute;left:308px;top:142px;width:190px;height:168px;border:1.5px solid var(--violet);border-radius:6px;padding:10px 14px;font-size:16px;line-height:1.2}
.section-band{font-size:19px}
.service{position:absolute;width:220px;display:flex;gap:14px}
.service .ico{flex:none;width:38px;height:38px;border:1.5px solid var(--cyan);border-radius:6px;margin-top:4px}
.service h3{font-size:15px;font-weight:600;margin-bottom:4px;white-space:nowrap}
.service p{font-size:11.5px;line-height:1.2;color:var(--muted);white-space:nowrap}
.divider-h{position:absolute;height:0;border-top:1.5px dashed var(--violet)}
.divider-v{position:absolute;width:0;border-left:1.5px dashed var(--violet)}
.reason{position:absolute;width:150px}
.reason-head{display:flex;gap:10px;align-items:flex-start;font-size:12.5px;font-weight:600;color:var(--cyan);line-height:1.15;min-height:44px}
.reason-dot{flex:none;width:28px;height:28px;border-radius:50%;background:var(--white);border:4px solid var(--purple)}
.reason p{font-size:11.5px;line-height:1.2;color:var(--muted);margin-top:6px;white-space:nowrap}
.rule-v{position:absolute;width:1.5px;background:rgba(123,44,245,.6)}
</style>
</head>
<body>

<!-- Outer spread: back + cover -->
<section class="spread spread--outer">
  <div class="page page--left">
    <div class="wordmark" style="left:165px;top:60px;width:220px;font-size:30px">tallow<br>brisko</div>
    <div class="echo" style="top:150px">Tallow Brisko</div>
    <div class="echo" style="top:174px">Tallow Brisko</div>
    <div class="echo" style="top:200px">Tallow Brisko</div>
    <div class="brand-title display">Tallow Brisko</div>
    <div class="tagline-box">Designs, die wirken. Marken, die bleiben.</div>

    <div class="band band--purple" style="left:37px;top:364px;width:270px;font-size:12.5px">Kontaktiere uns für eine<br>kostenlose Beratung!</div>

    <div class="contact" style="top:414px">
      <svg width="12" height="12" viewBox="0 0 12 12"><circle cx="6" cy="6" r="6" fill="#5b6cf0"/><path d="M4 3.5l1 1-.6.8c.5.9 1.1 1.5 2 2l.8-.6 1 1-.7.8C5.8 8.3 3.8 6.3 3.5 4.3z" fill="#fff"/></svg>
      <span>Kranichgasse 9<br>60594 Frankfurt</span>
    </div>
    <div class="contact" style="top:458px">
      <svg width="12" height="12" viewBox="0 0 12 12"><circle cx="6" cy="6" r="6" fill="#5b6cf0"/><path d="M6 2.8a2 2 0 0 1 2 2c0 1.4-2 3.6-2 3.6S4 6.2 4 4.8a2 2 0 0 1 2-2z" fill="#fff"/></svg>
      <span>+49 123 98410</span>
    </div>
    <div class="contact" style="top:486px">
      <svg width="12" height="12" viewBox="0 0 12 12"><circle cx="6" cy="6" r="6" fill="#5b6cf0"/><circle cx="6" cy="6" r="2.8" fill="none" stroke="#fff" stroke-width="1"/></svg>
      <span>hallo@tallowbrisko.de</span>
    </div>

    <div class="owner display"><small>Inhaber</small>Ilse Varn &amp; Jonas Beek</div>
    <div class="web-pill">www.tallowbrisko.de</div>
  </div>

  <div class="fold"></div>

  <div class="page page--right">
    <div class="wordmark" style="left:145px;top:40px;width:240px;font-size:44px">tallow<br>brisko</div>
    <div class="art" role="img" aria-label="Illustration: Bildschirm mit Designsoftware, Glühbirne, Farbpalette, Zahnrad und Schriftzeichen" style="left:90px;top:125px;width:360px;height:210px;background:radial-gradient(ellipse at 50% 55%,#8a5cf0 0%,#4a2cb0 45%,rgba(20,21,110,0) 75%)"></div>
    <div class="cover-line cover-line--small display">Dein Stil. Unser Design.</div>
    <div class="cover-line cover-line--big display">Unser Design</div>
    <div class="cover-web">www.tallowbrisko.de</div>
  </div>
</section>

<!-- Inner spread -->
<section class="spread spread--inner">
  <div class="page page--left">
    <div class="headline display">Modern, mutig, markant</div>
    <div class="lead"><strong>Tallow Brisko gestaltet</strong>die Zukunft deines<br>Unternehmensauftritts.</div>
    <div class="art" role="img" aria-label="Illustration: leuchtende Glühbirnen-Figur mit dem Schriftzug Ideen" style="left:35px;top:175px;width:265px;height:320px;background:radial-gradient(ellipse at 50% 50%,#ffd21f 0%,#f4a30d 40%,rgba(5,4,12,0) 72%)"></div>
    <div class="quote-box">Wir machen aus Ideen visuelle Erlebnisse und sorgen dafür, dass deine Marke im Gedächtnis bleibt.</div>
    <div class="art" role="img" aria-label="Illustration: Laptop mit Zeichenwerkzeugen und Farbfächer" style="left:290px;top:360px;width:215px;height:145px;background:radial-gradient(ellipse at 50% 55%,#d9c4f0 0%,#7a4fb8 45%,rgba(5,4,12,0) 75%)"></div>
  </div>

  <div class="fold"></div>

  <div class="page page--right">
    <div class="band band--purple section-band" style="left:30px;top:38px;width:280px">Unsere Leistungen</div>

    <div class="service" style="left:30px;top:92px">
      <div class="ico"></div>
      <div><h3>Next-Level Flyer</h3><p>Nicht nur Papier,<br>sondern deine<br>Botschaft im<br>perfekten Look.</p></div>
    </div>
    <div class="service" style="left:282px;top:94px">
      <div class="ico"></div>
      <div><h3>Corporate Identity</h3><p>Ein Design, das deine<br>Marke spricht<br>individuell, stark,<br>unvergesslich.</p></div>
    </div>
    <div class="divider-h" style="left:30px;top:184px;width:230px"></div>
    <div class="divider-h" style="left:282px;top:184px;width:208px"></div>
    <div class="divider-v" style="left:270px;top:88px;height:190px"></div>
    <div class="service" style="left:30px;top:206px">
      <div class="ico"></div>
      <div><h3>Digital &amp; Print</h3><p>Ob Social Media<br>Grafiken oder klass<br>isches Printdesign<br>wir sind da, wo du<br>uns brauchst.</p></div>
    </div>
    <div class="service" style="left:282px;top:208px">
      <div class="ico"></div>
      <div><h3>Alles aus einer Hand</h3><p>Logo, Farben,<br>Typografie, Flyer und<br>vieles mehr wir bauen<br>das Fundament für<br>deinen Erfolg</p></div>
    </div>

    <div class="band band--cyan section-band" style="left:30px;top:328px;width:270px">Warum wir?</div>

    <div class="reason" style="left:30px;top:384px">
      <div class="reason-head"><span class="reason-dot"></span><span>Dein Style,<br>unser<br>Know-how</span></div>
      <p>Wir kombinieren<br>deine Vision mit<br>moderner Ästhetik.</p>
    </div>
    <div class="rule-v" style="left:180px;top:384px;height:92px"></div>
    <div class="reason" style="left:205px;top:384px">
      <div class="reason-head"><span class="reason-dot"></span><span>Persönlicher<br>Service</span></div>
      <p>Wir hören zu und<br>setzen um, was dich<br>einzigartig macht</p>
    </div>
    <div class="rule-v" style="left:362px;top:384px;height:92px"></div>
    <div class="reason" style="left:380px;top:384px">
      <div class="reason-head"><span class="reason-dot"></span><span>Flexible<br>Lösungen</span></div>
      <p>für die<br>unterschiedlichsten<br>Anforderungen</p>
    </div>
  </div>
</section>

</body>
</html>
```